Gift Cards in the Mail Envelope

Mailing out gift cards in the envelope. Need an eye popping envelope. Please look at the enclosed images. The envelope should look like that.

Low design quality

```html
<!DOCTYPE html>
<html lang="en">
<head>
<meta charset="utf-8">
<title>Gift Card Envelope</title>
<link href="https://fonts.googleapis.com/css2?family=Lato:wght@400&display=swap" rel="stylesheet">
<style>
  :root {
    --bg: #e6e6e6;
    --paper: #ffffff;
    --gold: #bd830a;
    --rule: #a3a3a3;
    --text-light: #ffffff;
  }
  html, body {
    margin: 0;
    padding: 0;
    width: 1200px;
    height: 1200px;
    overflow: hidden;
    background: var(--bg);
  }
  .canvas {
    position: relative;
    width: 1200px;
    height: 1200px;
  }
  .envelope {
    position: absolute;
    background: var(--paper);
    box-shadow: 0 2px 4px rgba(0, 0, 0, 0.25);
  }
  .envelope-front {
    left: 190px;
    top: 192px;
    width: 819px;
    height: 409px;
  }
  .address-rule {
    position: absolute;
    left: 75px;
    width: 341px;
    height: 0;
    border-top: 1.5px solid var(--rule);
  }
  .address-rule.r1 { top: 60px; }
  .address-rule.r2 { top: 108px; }
  .address-rule.r3 { top: 156px; }
  .return-band {
    position: absolute;
    left: 0;
    bottom: 0;
    width: 100%;
    height: 49px;
    background: var(--gold);
  }
  .return-address {
    position: absolute;
    left: 75px;
    top: 12px;
    margin: 0;
    font-family: "Lato", sans-serif;
    font-size: 15.5px;
    color: var(--text-light);
    white-space: nowrap;
  }
  .envelope-back {
    left: 192px;
    top: 703px;
    width: 814px;
    height: 404px;
  }
  .envelope-back svg {
    position: absolute;
    left: 0;
    top: 0;
  }
  .flap { fill: var(--gold); }
</style>
</head>
<body>
<div class="canvas">
  <section class="envelope envelope-front">
    <div class="address-rule r1"></div>
    <div class="address-rule r2"></div>
    <div class="address-rule r3"></div>
    <div class="return-band">
      <p class="return-address">421, Address line goes here Country Name, 45452</p>
    </div>
  </section>
  <section class="envelope envelope-back">
    <svg width="814" height="404" viewBox="0 0 814 404" aria-hidden="true">
      <path class="flap" d="M7 0 H807 V33 Q807 50 792 57 L415 207 Q407 210 399 207 L22 57 Q7 50 7 33 Z"/>
    </svg>
  </section>
</div>
</body>
</html>
```